Stationery for Villa Marenta Design Hotel**

Who we are:

Wander on an isolated beach while breathing in the fresh, salty, sea air. Listen to the warm Pacific wind rustling through green palm trees as you walk to a pristine lagoon. Feel the delicious warmth of the sun kiss your skin; the beach is yours. At Villa Marenta you can experience a vacation in undisturbed, natural beauty. We have created a place for you to find new strength, relaxation, and inner harmony. We offer total rest to the experienced traveler from all over the world.

We are a brand new and smartly built design-hotel (under construction) close to a unique beach and a fantastic surf spot in Huatulco, Southwest Mexico.

As you can see in the attachments, we do have an established corporate design, but as for now still need a format for booklets for information around our hotel and things to do in the area, important numbers (we fill in the content for that one).

Our corporate colors:
green #64b445, brown #b07043, blue #0ab7cf, yellow # f9b02a and #fcc01a, navy #444f69
Corporate fonts:
Krub and Miller Banner.
For further information access:
www.villamarenta.example
https://slidevault.example/view/QmPxLwZrTyKsNbVcHdJe/

Social Media: VillaMarenta

Industry/Entity Type

Hotel

Font styles to use
Other font styles liked:
• Krub, Miller Banner

Requirements
Must have
• Stick to Logo Design, defined corporate elements, logo, colors, fonts and general touch and feel
Nice to have
• Who we are:

Our corporate colors:
Corporate fonts:
Krub and Miller Banner.
www.villamarenta.example

Social Media: VillaMarenta

```html
<!DOCTYPE html>
<html lang="en">
<head>
<meta charset="utf-8">
<title>Villa Marenta Design Hotel – Letterhead</title>
<link href="https://fonts.googleapis.com/css2?family=Tinos&display=swap" rel="stylesheet">
<style>
  :root{
    --backdrop:#d8dcdc;
    --paper:#ffffff;
    --teal:#1b8f99;
    --green:#7cc142;
    --orange:#e0a020;
    --brown:#b8763e;
    --gold:#e3a526;
    --grey:#b9bcbd;
    --ink:#4a4f58;
  }
  *{margin:0;padding:0;box-sizing:border-box}
  html,body{width:1200px;height:784px;overflow:hidden;background:var(--backdrop)}
  .stage{position:relative;width:1200px;height:784px}
  .letterhead{
    position:absolute;left:338px;top:22px;width:524px;height:740px;
    background:var(--paper);box-shadow:0 4px 18px rgba(0,0,0,.12);
    font-family:"Tinos",serif;color:var(--ink);overflow:hidden;
  }
  .edge-bar{position:absolute;width:5px;height:48px}
  .edge-bar--left{left:0}
  .edge-bar--right{right:0}
  .edge-bar--green{background:var(--green)}
  .edge-bar--teal{background:var(--teal)}

  .brand{position:absolute;left:40px;top:34px;display:flex;align-items:center;gap:8px}
  .brand__square{width:12px;height:12px;background:var(--gold)}
  .brand__name{font-size:20px;letter-spacing:1.5px;color:var(--gold);text-transform:uppercase}

  .contact{position:absolute;right:22px;top:28px;list-style:none;font-size:10.5px;line-height:15px}
  .contact li{display:flex;align-items:flex-start;gap:6px}
  .contact svg{width:10px;height:10px;flex:none;margin-top:2px}

  .footer-line{position:absolute}
  .footer-line--thin{height:3px;bottom:20px}
  .footer-line--thick{height:8px;bottom:0}
</style>
</head>
<body>
<div class="stage">
  <section class="letterhead">
    <span class="edge-bar edge-bar--left edge-bar--green" style="top:10px"></span>
    <span class="edge-bar edge-bar--left edge-bar--teal" style="top:66px"></span>
    <span class="edge-bar edge-bar--right edge-bar--green" style="top:290px"></span>
    <span class="edge-bar edge-bar--right edge-bar--teal" style="top:346px"></span>

    <header class="brand">
      <span class="brand__square"></span>
      <span class="brand__name">Villa Marenta</span>
    </header>

    <ul class="contact">
      <li>
        <svg viewBox="0 0 10 10"><circle cx="5" cy="5" r="5" fill="#1b8f99"/><path d="M5 2.2a1.8 1.8 0 0 1 1.8 1.8C6.8 5.4 5 7.8 5 7.8S3.2 5.4 3.2 4A1.8 1.8 0 0 1 5 2.2z" fill="#fff"/></svg>
        <span>Villa Marenta, Playa Serena,<br>Costa Azul, Oaxaca, Mexiko</span>
      </li>
      <li>
        <svg viewBox="0 0 10 10"><circle cx="5" cy="5" r="5" fill="#1b8f99"/><path d="M3.2 2.6l1 1-.6.8a4 4 0 0 0 2 2l.8-.6 1 1-.7.8C4.6 7.4 2.6 5.4 2.4 3.3z" fill="#fff"/></svg>
        <span>+52 1 (555) 014 2290</span>
      </li>
      <li>
        <svg viewBox="0 0 10 10"><circle cx="5" cy="5" r="5" fill="#1b8f99"/><rect x="2.6" y="3.3" width="4.8" height="3.4" fill="#fff"/><path d="M2.6 3.3L5 5.2l2.4-1.9" stroke="#1b8f99" stroke-width=".6" fill="none"/></svg>
        <span>hello@villamarenta.example</span>
      </li>
      <li>
        <svg viewBox="0 0 10 10"><circle cx="5" cy="5" r="5" fill="#1b8f99"/><circle cx="5" cy="5" r="2.6" fill="none" stroke="#fff" stroke-width=".6"/><path d="M2.4 5h5.2M5 2.4c-1.2 1.4-1.2 3.8 0 5.2M5 2.4c1.2 1.4 1.2 3.8 0 5.2" stroke="#fff" stroke-width=".5" fill="none"/></svg>
        <span>www.villamarenta.example</span>
      </li>
    </ul>

    <span class="footer-line footer-line--thin" style="left:0;width:140px;background:var(--orange)"></span>
    <span class="footer-line footer-line--thin" style="left:146px;width:188px;background:var(--green)"></span>
    <span class="footer-line footer-line--thin" style="left:340px;width:184px;background:var(--brown)"></span>
    <span class="footer-line footer-line--thick" style="left:0;width:334px;background:var(--teal)"></span>
    <span class="footer-line footer-line--thick" style="left:334px;width:190px;background:var(--grey)"></span>
  </section>
</div>
</body>
</html>
```